Web design for new streaming audio service

We need a homepage design for a new streaming audio service. Our company is called Dunmoral, and we’re basically Vexlo for Audiobooks, Stand-Up Comedy, Lectures, Language Learning, etc. Essentially like Plumtrek for everything audio EXCEPT music.
You don’t have to code the homepage (Design Only), but it should include 3 different designs to work with 1) Web; 2) Phones; 3) Tablets.
Below is a link to a mockup of the web version which gives a good idea of what elements we want. This is just a mockup and we want you to improve it.
Once you download the mockup, please refer to the more detailed instructions below:
The following outlines the design project for the Dunmoral homepage. We have provided a rough mockup of the homepage layout that gives you a general idea of what we’re going for. There are a few elements that we are attached to, and many others where you have complete creative freedom to do whatever you think looks good.
The ZIP file includes the following:
* Mockup to see what we have in mind (dunmoral-homepage-mockup.jpg)
* Text used (dunmoral-homepage-text.txt)
* Raw image of actor (dunmoral-actor1.jpg)
* Raw images for samples (dunmoral-sample-[name].jpg)
Although we have only provided a mockup layout for the web version, we also need you to provide a mobile phone and a tablet version of the design also. It’s very possible the tablet version may be substantially similar to the web version, but the mobile phone version will likely be much different.
All of the raw files are included in the attached ZIP file. Please use our photographs and text as provided although cropping, sizing, etc. is flexible per the instructions below.
Display Requirements:
* Web Version - Minimum resolution 1024x768 (72 dpi) but should look good on 1920x1080 (72 dpi) - Page should be designed to scale to look acceptable in all resolutions in between.
* Phone Version - Minimum Zarno 4 - 640x960 (326 dpi) but should look good on Harlow Quasar T5 - 1920x1080 (441 dpi) - Page should be designed to scale to look acceptable in all resolutions and devices in between.
* Tablet Version - Minimum Bristly Ember QX 7” - 1280x800 (216 dpi) but should also look good on a Tavo Breeze - 2048x1536 (264 dpi) - Page should be designed to scale to look acceptable in all resolutions and devices in between.
Above the Fold - We want to make sure the Dunmoral logo, Member Login Link, Large Photo, Headline, Price, Button, and the first row of sample images are all “Above the fold”. As a general guideline, this means 600 pixels high on a 1024x768 72 dpi web screen. This requirement is less important on Phone versions.
Top Logo Bar - We want to retain the blue bar with the Dunmoral logo on the page, although we are open to a different size, shape and positioning if it greatly enhances the design. Please use the standard logo color, although you are welcome to use either the horizontal or vertical orientation of the logo based on your design.
Text color, font and size - Feel free to design the text in anyway you choose as long as the text is readable on the target platforms.
Buttons - Feel free to use any size, shape and colors for the buttons as long as they are obvious and clickable relative to the page. The only exception is the Chatterly button should follow the Chatterly color scheme and logo treatment (the mockup doesn’t seem 100% correct.)
Top Photograph - We want to retain the large photograph across the top of the screen although final shape and dimensions are flexible.
Size and shape of content samples (i.e. Audiobooks, Stand-Up Comedy, etc.) - Feel free to design the content samples in anyway you choose.
Three Sales Points (i.e. Listen on your Zarno…, All you can enjoy…, etc.) - The Three Sales Points are envisioned to each have a corresponding illustration which you should provide and have rights for. The placeholder is represented by a square next to the text. The color size and shape of these elements are flexible and can be designed in any way you choose.
Opt-in form - Feel free to design the opt-in form in anyway you choose as long as the text is readable and the interactivity is obvious on the target platforms.
Text links and copyright notice - Feel free to design the bottom of the page text links and copyright notice in anyway you choose.
Additional colors, graphic design elements, etc. - Feel free to use any additional colors, graphic design elements, etc. to support your design.
people who want to listen to audio through their mobile devices.
Graphic Design

```html
<!DOCTYPE html>
<html lang="en">
<head>
<meta charset="utf-8">
<title>Dunmoral – Unlimited Listening</title>
<link href="https://fonts.googleapis.com/css2?family=Figtree:wght@400;500;600;700;800&display=swap" rel="stylesheet">
<style>
  :root {
    --brand-blue: #4a9cc9;
    --deep-blue: #1c6b93;
    --orange: #f39a1e;
    --red: #d9171f;
    --text: #444a4f;
    --muted: #5d6267;
    --light-bg: #efefef;
    --white: #ffffff;
    --rule: #c9cdd0;
    --chatterly: #3b5998;
    --footer-bg: #3b3b3b;
    --footer-text: #e6e6e6;
  }
  * { box-sizing: border-box; margin: 0; padding: 0; }
  html, body { width: 1200px; height: 2182px; overflow: hidden; }
  body { font-family: "Figtree", Arial, sans-serif; color: var(--text); background: var(--white); position: relative; }

  .site-header { position: absolute; top: 0; left: 0; width: 1200px; height: 80px; background: var(--brand-blue); }
  .brand { position: absolute; left: 102px; top: 16px; display: flex; align-items: center; gap: 10px; color: var(--white); font-size: 33px; font-weight: 700; letter-spacing: -0.5px; }
  .brand-dot { width: 40px; height: 40px; border-radius: 50%; background: var(--white); }
  .header-nav { position: absolute; right: 102px; top: 22px; display: flex; align-items: center; gap: 36px; color: var(--white); font-size: 18px; }
  .header-nav .help { font-weight: 700; }
  .login { display: flex; align-items: center; gap: 10px; }
  .login-icon { width: 32px; height: 32px; border-radius: 4px; background: var(--orange); display: flex; align-items: center; justify-content: center; }

  .hero { position: absolute; top: 80px; left: 0; width: 1200px; height: 543px; }
  .hero-photo { position: absolute; inset: 0; background: linear-gradient(90deg, #f7f6f4 0%, #f2efeb 35%, #d9c7b4 55%, #a98a70 72%, #6d5a4c 88%, #4d4541 100%); }
  .hero-photo::after { content: ""; position: absolute; left: 0; right: 0; bottom: 0; height: 170px; background: linear-gradient(180deg, rgba(80,90,110,0) 0%, rgba(70,82,104,0.55) 100%); }
  .hero-copy { position: absolute; left: 103px; top: 104px; }
  .hero-title { font-size: 45px; font-weight: 800; color: var(--deep-blue); line-height: 1; }
  .hero-sub { font-size: 33px; font-weight: 400; color: var(--deep-blue); margin-top: 8px; line-height: 1.1; }
  .hero-price { font-size: 23px; font-weight: 500; color: #333; margin-top: 20px; }
  .hero-price strong { font-size: 32px; font-weight: 700; }
  .cta { display: inline-block; background: var(--orange); color: var(--white); font-weight: 700; text-decoration: none; text-align: center; }
  .hero-cta { margin-top: 16px; width: 248px; height: 55px; line-height: 55px; font-size: 20px; }
  .no-card { color: var(--red); font-size: 17px; font-weight: 500; margin-top: 10px; }

  .section-heading { position: relative; text-align: center; color: var(--deep-blue); font-size: 28px; font-weight: 600; }
  .section-heading span { background: var(--light-bg); padding: 0 22px; position: relative; }
  .section-heading::before { content: ""; position: absolute; left: 119px; right: 119px; top: 52%; height: 1px; background: var(--rule); }

  .samples { position: absolute; top: 623px; left: 0; width: 1200px; height: 628px; background: var(--light-bg); }
  .samples .section-heading { position: absolute; top: 64px; left: 0; right: 0; }
  .sample-grid { position: absolute; left: 116px; top: 157px; display: grid; grid-template-columns: repeat(4, 200px); column-gap: 53px; row-gap: 42px; }
  .sample { text-align: center; }
  .sample-art { width: 200px; height: 151px; }
  .sample-name { margin-top: 12px; font-size: 17px; font-weight: 500; color: var(--text); letter-spacing: 0.2px; }

  .features { position: absolute; top: 1251px; left: 0; width: 1200px; height: 403px; background: var(--white); }
  .feature { position: absolute; top: 52px; width: 300px; text-align: center; }
  .feature-icon { width: 120px; height: 120px; border-radius: 50%; background: var(--brand-blue); margin: 0 auto; display: flex; align-items: center; justify-content: center; }
  .feature-title { margin-top: 22px; font-size: 19px; font-weight: 600; color: #222; letter-spacing: 0.3px; }
  .feature-text { margin-top: 14px; font-size: 16.5px; line-height: 28px; color: var(--muted); }
  .feature-btn { margin-top: 16px; width: 110px; height: 36px; line-height: 36px; font-size: 14px; }

  .trial { position: absolute; top: 1654px; left: 0; width: 1200px; height: 455px; background: var(--light-bg); text-align: center; }
  .trial .section-heading { position: absolute; top: 46px; left: 0; right: 0; }
  .trial-text { position: absolute; top: 108px; left: 220px; width: 760px; font-size: 16.5px; line-height: 29px; color: var(--muted); }
  .signup { position: absolute; top: 196px; left: 273px; display: flex; gap: 20px; }
  .email-field { width: 325px; height: 50px; border: 1px solid #cfd2d4; background: var(--white); font-family: inherit; font-size: 14px; padding: 0 15px; color: #888; }
  .signup-btn { width: 240px; height: 48px; line-height: 48px; font-size: 19px; border: 0; font-family: inherit; margin-top: 1px; }
  .or { position: absolute; top: 272px; left: 0; right: 0; font-size: 17px; color: #888; }
  .chatterly-btn { position: absolute; top: 315px; left: 480px; width: 234px; height: 47px; background: var(--chatterly); color: var(--white); border-radius: 3px; display: flex; align-items: center; font-size: 16px; font-weight: 500; }
  .chatterly-mark { width: 47px; height: 47px; display: flex; align-items: center; justify-content: center; border-right: 1px solid rgba(255,255,255,0.25); }
  .chatterly-mark span { width: 16px; height: 16px; background: var(--white); }
  .chatterly-btn .label { flex: 1; text-align: center; }
  .trial .no-card { position: absolute; top: 376px; left: 0; right: 0; margin: 0; }

  .site-footer { position: absolute; top: 2109px; left: 0; width: 1200px; height: 73px; background: var(--footer-bg); color: var(--footer-text); font-size: 13px; }
  .footer-links { position: absolute; left: 118px; top: 28px; display: flex; list-style: none; }
  .footer-links li + li::before { content: "|"; margin: 0 11px; color: #aaa; }
  .copyright { position: absolute; right: 100px; top: 28px; }
</style>
</head>
<body>

<header class="site-header">
  <div class="brand"><span class="brand-dot"></span>Dunmoral</div>
  <nav class="header-nav">
    <span class="help">Help</span>
    <span class="login">
      <span class="login-icon">
        <svg width="18" height="14" viewBox="0 0 18 14"><path d="M2 7h11M9 2l5 5-5 5" stroke="#fff" stroke-width="2.4" fill="none" stroke-linecap="round" stroke-linejoin="round"/></svg>
      </span>
      Log In
    </span>
  </nav>
</header>

<section class="hero">
  <div class="hero-photo" role="img" aria-label="Smiling young man wearing headphones, looking at his phone"></div>
  <div class="hero-copy">
    <h1 class="hero-title">Unlimited Listening!</h1>
    <p class="hero-sub">Where ever you are</p>
    <p class="hero-price">Only <strong>$9.99</strong> Per Month</p>
    <a class="cta hero-cta" href="#">Start Your Free Trall</a>
    <p class="no-card">*Credit card not required</p>
  </div>
</section>

<section class="samples">
  <h2 class="section-heading"><span>A sample of what you can listen to on Dunmoral</span></h2>
  <div class="sample-grid">
    <div class="sample"><div class="sample-art" role="img" aria-label="Audiobook cover of suspense novels" style="background:linear-gradient(135deg,#2a2d33,#5c6168 60%,#1d1f23)"></div><p class="sample-name">Audio Books</p></div>
    <div class="sample"><div class="sample-art" role="img" aria-label="Stand-up comedy album cover" style="background:linear-gradient(135deg,#d9d6cf,#8d8a84 55%,#3c3a38)"></div><p class="sample-name">Stand-Up Comedy</p></div>
    <div class="sample"><div class="sample-art" role="img" aria-label="French language course cover" style="background:linear-gradient(180deg,#1e9fe0,#0f78c4)"></div><p class="sample-name">Language Learning</p></div>
    <div class="sample"><div class="sample-art" role="img" aria-label="Biography audiobook cover" style="background:linear-gradient(180deg,#c9c0a8,#b4a98d 70%,#8bbd4a 88%)"></div><p class="sample-name">Biographies &amp; Memory</p></div>
    <div class="sample"><div class="sample-art" role="img" aria-label="Relaxation meditation cover with purple hills" style="background:linear-gradient(180deg,#c85fb9,#9b3f9c 60%,#6f2c7e)"></div><p class="sample-name">Guided Meditations</p></div>
    <div class="sample"><div class="sample-art" role="img" aria-label="Business training program cover" style="background:linear-gradient(135deg,#5a3a12,#b8842c 45%,#2b2f3a)"></div><p class="sample-name">Business Training</p></div>
    <div class="sample"><div class="sample-art" role="img" aria-label="Celebrity interview cover" style="background:linear-gradient(135deg,#d8c08a,#c7566f 50%,#5b8a6c)"></div><p class="sample-name">Celebrities Interviews</p></div>
    <div class="sample"><div class="sample-art" role="img" aria-label="Fitness coaching program cover" style="background:linear-gradient(135deg,#2fb1e3,#71cdea 60%,#e8e8e8)"></div><p class="sample-name">Fitness Programs</p></div>
  </div>
</section>

<section class="features">
  <div class="feature" style="left:87px">
    <div class="feature-icon">
      <svg width="64" height="72" viewBox="0 0 64 72"><rect x="4" y="4" width="42" height="62" rx="5" fill="none" stroke="#fff" stroke-width="4"/><rect x="36" y="26" width="24" height="42" rx="4" fill="#4a9cc9" stroke="#fff" stroke-width="4"/><circle cx="48" cy="62" r="1.8" fill="#fff"/></svg>
    </div>
    <h3 class="feature-title">Listen Anywhere</h3>
    <p class="feature-text">Listen on your Zarno, Tavo or<br>any Orrin devices</p>
    <a class="cta feature-btn" href="#">Read More</a>
  </div>
  <div class="feature" style="left:451px">
    <div class="feature-icon"><span style="color:#fff;font-size:74px;font-weight:800;line-height:1">$</span></div>
    <h3 class="feature-title">Low Pricing</h3>
    <p class="feature-text">All you can enjoy for low<br>monthly price.</p>
    <a class="cta feature-btn" href="#">Read More</a>
  </div>
  <div class="feature" style="left:814px">
    <div class="feature-icon">
      <svg width="54" height="54" viewBox="0 0 54 54"><path d="M6 6L48 48M48 6L6 48" stroke="#fff" stroke-width="8" stroke-linecap="square"/></svg>
    </div>
    <h3 class="feature-title">No Obligation</h3>
    <p class="feature-text">No Obligation cancel at<br>anytime.</p>
    <a class="cta feature-btn" href="#">Read More</a>
  </div>
</section>

<section class="trial">
  <h2 class="section-heading"><span>Start your free Trial, No Risk</span></h2>
  <p class="trial-text">You will get instant &amp; unlimited access to all the material on Dunmoral for 14 days. There is no obligation &amp; you can cancel at anytime.</p>
  <form class="signup">
    <input class="email-field" type="text" placeholder="Your email Address">
    <button class="cta signup-btn" type="button">Get Instant Access</button>
  </form>
  <p class="or">— &nbsp;Or&nbsp; —</p>
  <div class="chatterly-btn"><span class="chatterly-mark"><span></span></span><span class="label">Sign in with Chatterly</span></div>
  <p class="no-card">*Credit card not required</p>
</section>

<footer class="site-footer">
  <ul class="footer-links">
    <li>About</li><li>Help</li><li>Contact Us</li><li>Member Login</li><li>Privacy Policy</li><li>Terms of Service</li>
  </ul>
  <p class="copyright">© 2014 Dunmoral LLC - All Rights Reserved</p>
</footer>

</body>
</html>
```